Design a building access mobile app for Quillo by Tamberlin Entry Systems

Hello, We're looking for an awesome designer to create an app design for our app Quillo, by Tamberlin Entry Systems. the mobile app allows employees open their office doors with their mobile phone. this means they don't have to use those plastic card badges or keys. We like clean modern design, dark and light themes. We don't have a logo yet.
Updates

Reason: Waiting on a couple designers to submit concepts

Target Market(s)

Commercial and employees

Industry/Entity Type

Building

Font styles to use
Sans Serif
Other font styles liked:
• Oswald extra light

Requirements
Must have
• nice clean design

```html
<!DOCTYPE html>
<html lang="en">
<head>
<meta charset="utf-8">
<title>Tamberlin Security – Door Access</title>
<link rel="stylesheet" href="https://fonts.googleapis.com/css2?family=Oswald:wght@300;400&family=Inter:wght@400;600&display=swap">
<style>
  :root {
    --bg-top: #c41a33;
    --bg-bottom: #b3142c;
    --field-bg: rgba(255, 255, 255, 0.16);
    --field-line: rgba(255, 255, 255, 0.22);
    --button-red: #dc2140;
    --button-glow: rgba(255, 120, 140, 0.35);
    --white: #ffffff;
    --white-soft: rgba(255, 255, 255, 0.78);
    --pin-green: #7ed321;
    --version-ink: rgba(120, 10, 25, 0.55);
  }
  * { margin: 0; padding: 0; box-sizing: border-box; }
  html, body { width: 675px; height: 1200px; overflow: hidden; }
  body {
    position: relative;
    background: linear-gradient(180deg, var(--bg-top) 0%, var(--bg-bottom) 100%);
    color: var(--white);
    font-family: "Oswald", "Arial Narrow", sans-serif;
  }
  .status-bar {
    position: absolute; left: 0; top: 0; width: 675px; height: 45px;
    font-family: "Inter", "Helvetica Neue", sans-serif;
    font-size: 25px; font-weight: 600;
    display: flex; align-items: center; justify-content: space-between;
    padding: 0 14px;
  }
  .status-left { display: flex; align-items: center; gap: 10px; }
  .signal { display: flex; gap: 4px; }
  .signal span { width: 10px; height: 10px; border-radius: 50%; background: var(--white); }
  .signal span.off { background: none; border: 1.5px solid var(--white); }
  .status-time { position: absolute; left: 0; right: 0; text-align: center; pointer-events: none; }
  .status-right { display: flex; align-items: center; gap: 8px; }
  .battery { width: 46px; height: 20px; border: 2px solid var(--white); border-radius: 4px; padding: 2px; position: relative; }
  .battery::after { content: ""; position: absolute; right: -6px; top: 5px; width: 3px; height: 7px; background: var(--white); border-radius: 0 2px 2px 0; }
  .battery span { display: block; width: 100%; height: 100%; background: var(--white); border-radius: 1px; }

  .nav-bar {
    position: absolute; left: 0; top: 45px; width: 675px; height: 54px;
    display: flex; align-items: center; justify-content: center;
  }
  .nav-menu { position: absolute; left: 26px; top: 14px; }
  .nav-info { position: absolute; right: 24px; top: 10px; }
  .nav-title { font-size: 33px; font-weight: 400; letter-spacing: 0.3px; }

  .location-field {
    position: absolute; left: 50px; top: 176px; width: 576px; height: 68px;
    background: var(--field-bg);
    border-bottom: 2px solid var(--field-line);
    border-radius: 4px;
    display: flex; align-items: center; justify-content: space-between;
    padding: 0 24px 0 22px;
  }
  .location-placeholder { font-size: 28px; font-weight: 300; color: var(--white-soft); }

  .door-button {
    position: absolute; left: 164px; top: 502px; width: 346px; height: 346px;
    border-radius: 50%;
    background: radial-gradient(circle at 50% 45%, #e2264a 0%, var(--button-red) 70%, #d11d3a 100%);
    box-shadow: 0 0 0 14px var(--button-glow), 0 0 60px 20px rgba(255, 90, 110, 0.25);
    display: flex; flex-direction: column; align-items: center;
  }
  .door-icon { margin-top: 48px; }
  .door-label { margin-top: 16px; font-size: 38px; font-weight: 400; }

  .app-version {
    position: absolute; left: 0; right: 0; top: 1152px;
    text-align: center; font-family: "Inter", sans-serif; font-size: 22px;
    color: var(--version-ink);
  }
</style>
</head>
<body>
  <header class="status-bar">
    <div class="status-left">
      <div class="signal"><span></span><span></span><span></span><span></span><span class="off"></span></div>
      <svg width="26" height="20" viewBox="0 0 26 20" aria-hidden="true">
        <path d="M13 18 L9 14 A6 6 0 0 1 17 14 Z" fill="#fff"/>
        <path d="M5 10 A11 11 0 0 1 21 10" stroke="#fff" stroke-width="2.6" fill="none"/>
        <path d="M1 6 A17 17 0 0 1 25 6" stroke="#fff" stroke-width="2.6" fill="none"/>
      </svg>
    </div>
    <div class="status-time">9:41 PM</div>
    <div class="status-right">
      <svg width="14" height="22" viewBox="0 0 14 22" aria-hidden="true"><path d="M2 6 L12 16 L7 21 V1 L12 6 L2 16" stroke="#fff" stroke-width="2" fill="none"/></svg>
      <span>100%</span>
      <div class="battery"><span></span></div>
    </div>
  </header>

  <nav class="nav-bar">
    <svg class="nav-menu" width="34" height="26" viewBox="0 0 34 26" aria-label="Menu">
      <rect x="0" y="1" width="34" height="3" fill="#fff"/>
      <rect x="0" y="11.5" width="34" height="3" fill="#fff"/>
      <rect x="0" y="22" width="34" height="3" fill="#fff"/>
    </svg>
    <h1 class="nav-title">Tamberlin Security</h1>
    <svg class="nav-info" width="30" height="30" viewBox="0 0 30 30" aria-label="Info">
      <circle cx="15" cy="15" r="13" stroke="#fff" stroke-width="2" fill="none"/>
      <circle cx="15" cy="9" r="1.7" fill="#fff"/>
      <rect x="13.8" y="13" width="2.4" height="10" fill="#fff"/>
    </svg>
  </nav>

  <div class="location-field">
    <span class="location-placeholder">Enter your office location</span>
    <svg width="28" height="38" viewBox="0 0 28 38" aria-label="Location pin">
      <path d="M14 1 C6.5 1 1 6.6 1 13.8 C1 23 14 37 14 37 C14 37 27 23 27 13.8 C27 6.6 21.5 1 14 1 Z" fill="var(--pin-green)"/>
      <circle cx="14" cy="13.5" r="5" fill="#b3142c"/>
    </svg>
  </div>

  <button class="door-button" style="border:none;color:inherit;font:inherit;">
    <svg class="door-icon" width="96" height="150" viewBox="0 0 96 150" aria-label="Open door">
      <path d="M8 146 V4 H88 V146" stroke="#fff" stroke-width="7" fill="none" stroke-linejoin="miter"/>
      <path d="M8 4 L60 22 V146 L8 130 Z" fill="#fff"/>
      <circle cx="49" cy="80" r="3.5" fill="var(--button-red)"/>
    </svg>
    <span class="door-label">Door</span>
  </button>

  <footer class="app-version">v781</footer>
</body>
</html>
```